New Business Card Design for Manufacturing

We are an engineering/manufacturing company that offers Advanced machining/assembly/engineering services, as well as innovative products for the heavy duty engine cooling markets.

We are looking to get a new business card designed that is clean and modern looking, but still fits the wide range of technical/skilled work we do.

- We hope to use this design as the base for other design work in new Presentations, web, and print work.

Industry/Entity Type

Engineering

Contact Information for Business Card

Our preferred color of blue is (RGB) 22/71/159 but can vary slightly from that color. Our content will be our Logo and full company name (Vantrell Forge Works, Inc.), company address, name, job title, phone number with extension, cell number, fax number, website, and email address on the cards.
We'd like the full company name next to the logo, but we are open to other interpretations of that layout.
Preferably, we would like the back side to be clean with just our logo, and the front to contain all of the contact information.

Colors
2f74b4
0355a3
85abd2

Requirements
Must have
• - Logo, company name, needed content - We are open to interpretation beyond that.
• - Standard size business card.
• - Horizontal orientation.
• - Enough space for lengthy names / job titles (for example, a job title could read "Directory of Human Resources" or "V.P. of Governmental Affairs"). We need this to look clean, whether the title be short (CEO) or long (as described above).

```html
<!DOCTYPE html>
<html lang="en">
<head>
<meta charset="utf-8">
<title>Vantrell Forge Works, Inc. – Business Card</title>
<link href="https://fonts.googleapis.com/css2?family=Archivo:wght@800&family=Lato:wght@400;700&display=swap" rel="stylesheet">
<style>
  :root {
    --brand-blue: #1647a0;
    --mid-blue: #0355a3;
    --light-blue: #85abd2;
    --card-white: #ffffff;
    --page-bg: #e6e8ec;
  }
  * { box-sizing: border-box; margin: 0; padding: 0; }
  html, body {
    width: 1200px; height: 880px; overflow: hidden;
    background: var(--page-bg);
  }
  .sheet { position: relative; width: 1200px; height: 880px; }
  .card {
    position: absolute; left: 260px;
    width: 680px; height: 388px;
    background: var(--card-white);
    border-radius: 22px; overflow: hidden;
    box-shadow: 0 6px 18px rgba(0,0,0,0.12);
  }
  .card--back { top: 40px; }
  .card--front { top: 452px; }

  .brand {
    position: absolute; display: flex; align-items: center; gap: 12px;
    font-family: "Archivo", sans-serif; font-weight: 800;
    color: var(--brand-blue); text-transform: uppercase;
    letter-spacing: 0.5px; line-height: 1.1;
  }
  .brand__mark { width: 34px; height: 34px; background: var(--brand-blue); flex: none; }
  .card--back .brand { left: 170px; top: 150px; font-size: 32px; }
  .card--front .brand { left: 56px; top: 58px; font-size: 24px; }

  .card__waves { position: absolute; inset: 0; width: 100%; height: 100%; }

  .person {
    position: absolute; left: 60px; top: 205px;
    font-family: "Lato", sans-serif; color: var(--brand-blue);
  }
  .person__name {
    font-family: "Archivo", sans-serif; font-weight: 800;
    font-size: 21px; text-transform: uppercase; letter-spacing: 0.5px;
  }
  .person__title { font-size: 16px; margin-top: 2px; }

  .contact {
    position: absolute; right: 26px; top: 165px;
    font-family: "Lato", sans-serif; color: var(--card-white);
    font-size: 14px; text-align: right; line-height: 1.5;
    list-style: none;
  }
  .contact__address { margin-bottom: 3px; }
  .contact__item { display: flex; align-items: center; justify-content: flex-end; gap: 8px; }
  .contact__icon { width: 17px; height: 17px; flex: none; }
</style>
</head>
<body>
<main class="sheet">

  <section class="card card--back" aria-label="Card back">
    <div class="brand">
      <span class="brand__mark"></span>
      <span class="brand__name">Vantrell Forge<br>Works, Inc.</span>
    </div>
  </section>

  <section class="card card--front" aria-label="Card front">
    <svg class="card__waves" viewBox="0 0 680 388" preserveAspectRatio="none" aria-hidden="true">
      <path d="M0 320 C150 300 300 250 360 150 C330 250 200 330 0 345 Z" fill="var(--light-blue)"/>
      <path d="M0 355 C210 345 340 300 380 190 C420 90 500 30 610 0 L680 0 L680 388 L0 388 Z" fill="var(--brand-blue)"/>
      <path d="M130 388 C330 360 400 290 440 190 C480 90 560 30 650 0" fill="none" stroke="var(--card-white)" stroke-width="7"/>
    </svg>

    <div class="brand">
      <span class="brand__mark"></span>
      <span class="brand__name">Vantrell Forge<br>Works, Inc.</span>
    </div>

    <div class="person">
      <p class="person__name">Dorian Keller</p>
      <p class="person__title">Founder</p>
    </div>

    <ul class="contact">
      <li class="contact__address">PO Box 418<br>Harlow Lane, Eastbrook</li>
      <li class="contact__item">(555) 214-0387
        <svg class="contact__icon" viewBox="0 0 18 18"><circle cx="9" cy="9" r="8" fill="none" stroke="#fff" stroke-width="1.3"/><rect x="6" y="4" width="6" height="10" rx="1.2" fill="none" stroke="#fff" stroke-width="1.2"/></svg>
      </li>
      <li class="contact__item">(555) 214-0391
        <svg class="contact__icon" viewBox="0 0 18 18"><circle cx="9" cy="9" r="8" fill="none" stroke="#fff" stroke-width="1.3"/><rect x="5" y="7" width="8" height="5" fill="#fff"/><rect x="6.5" y="4.5" width="5" height="2.5" fill="#fff"/></svg>
      </li>
      <li class="contact__item">hello@vantrellforge.com
        <svg class="contact__icon" viewBox="0 0 18 18"><circle cx="9" cy="9" r="8" fill="none" stroke="#fff" stroke-width="1.3"/><rect x="5" y="6" width="8" height="6" fill="none" stroke="#fff" stroke-width="1.2"/><path d="M5 6 L9 9.5 L13 6" fill="none" stroke="#fff" stroke-width="1.2"/></svg>
      </li>
      <li class="contact__item">www.vantrellforge.com
        <svg class="contact__icon" viewBox="0 0 18 18"><circle cx="9" cy="9" r="8" fill="none" stroke="#fff" stroke-width="1.3"/><circle cx="9" cy="9" r="4.5" fill="none" stroke="#fff" stroke-width="1.1"/><path d="M4.5 9 H13.5 M9 4.5 V13.5" stroke="#fff" stroke-width="1.1"/></svg>
      </li>
    </ul>
  </section>

</main>
</body>
</html>
```